Design a Google site for a travel agency

I own a travel agency and I would like to have a Google site built for my company called Harborquestjourneys.com by Bright Path Holidays. Our specialty Cruising and adventure. We create a lot of custom tour of Europe and Peru. Our Adventure tours targets mainly women from 25 to 65. I would like to site especially the cruise to appeal to family but also upscale more expensive upscale clientele.
Updates

I would like to shift away from create a new site with multiple pages to one simple Google Site page with a Contact us page and testimonials. The sites theme is Cruise & Adventure Travel. We specialize in selling cruises and building custom travel tours around the world.

Target Market(s)

Cruisers and adventure travelers for women from 25 to 70

Industry/Entity Type

travel industry with a focus on cruising and adventure travel

Coding

Coded - Design and coding required

Number of Pages Required

5+ page

Font styles to use
Serif
Sans Serif

Requirements
Must have
• Home page, Cruise, Adventure Tours, Testimonials, About Us
Nice to have
• Auto place https://www.brightpathholidays.ca/offers into the site.
Should not have
• beach resorts

```html
<!DOCTYPE html>
<html lang="en">
<head>
<meta charset="utf-8">
<title>Bright Path Holidays – Cruise &amp; Adventure Travel</title>
<link rel="stylesheet" href="https://fonts.googleapis.com/css2?family=Cinzel:wght@400;700&family=Roboto:wght@400;500;700&display=swap">
<style>
:root{
  --blue:#229fd9;
  --orange:#f7a21b;
  --green:#8dc63f;
  --gold:#e8a22a;
  --ink:#333333;
  --muted:#6f6f6f;
  --soft:#f4f4f4;
  --white:#ffffff;
}
*{margin:0;padding:0;box-sizing:border-box}
html,body{width:1200px;height:3958px;overflow:hidden}
body{position:relative;font-family:"Roboto",Arial,sans-serif;color:var(--ink);background:var(--white)}
.abs{position:absolute}
.serif{font-family:"Cinzel",Georgia,serif;text-transform:uppercase}

/* header */
.site-header{left:0;top:0;width:1200px;height:111px;background:var(--white)}
.brand{left:111px;top:36px;display:flex;align-items:center;gap:10px}
.brand-dot{width:32px;height:32px;border-radius:50%;background:var(--orange)}
.brand-name{font-size:18px;font-weight:500;color:var(--blue);white-space:nowrap}
.nav{left:443px;top:37px;width:612px;height:35px;display:flex;align-items:center;justify-content:space-between}
.nav a{font-size:13px;font-weight:700;color:var(--ink);text-decoration:none;text-transform:uppercase;white-space:nowrap;line-height:35px}
.nav a.active{background:var(--green);color:var(--white);width:84px;text-align:center}
.search{left:1073px;top:47px}

/* hero */
.hero{left:0;top:111px;width:1200px;height:557px;background:linear-gradient(180deg,#5d5a7a 0%,#c98a7e 28%,#6b7890 45%,#3d4350 70%,#2c2a2a 100%)}
.hero-title{left:0;top:322px;width:1200px;text-align:center;color:var(--white);font-size:60px;font-weight:700;line-height:1}
.hero-sub{left:0;top:392px;width:1200px;text-align:center;color:var(--white);font-size:32px;font-weight:700;line-height:1}
.hero-rule{left:545px;top:444px;width:110px;height:4px;background:var(--gold)}

/* section titles */
.section-title{left:0;width:1200px;text-align:center;color:var(--blue);font-size:38px;font-weight:700;line-height:1}
.section-sub{left:0;width:1200px;text-align:center;color:#555;font-size:18px}

.tile{width:309px;height:222px}
.tile-label{width:309px;text-align:center;font-size:20px;font-weight:500;color:var(--ink)}

/* about */
.about-band{left:0;top:1512px;width:1200px;height:513px;background:var(--soft)}
.about-title{left:665px;top:1645px;color:var(--blue);font-size:38px;font-weight:700;line-height:1}
.about-text{left:665px;top:1712px;width:424px;font-size:13px;line-height:26px;color:var(--muted);text-align:justify}

/* magazines */
.mag-band{left:0;top:2025px;width:1200px;height:475px;background:var(--orange)}
.mag-title{left:220px;top:2090px;color:var(--white);font-size:34px;font-weight:700;line-height:1}
.mag-sub{left:220px;top:2140px;color:var(--white);font-size:18px}
.cover{border:3px solid var(--white);height:230px;top:2202px}

/* blogs */
.blog-band{left:0;top:3131px;width:1200px;height:636px;background:var(--soft)}
.btn{left:533px;top:3288px;width:132px;height:51px;background:var(--green);color:var(--white);font-size:14px;font-weight:500;text-align:center;line-height:51px}
.blog-head{width:309px;text-align:center;font-size:15px;font-weight:500;top:3380px}
.blog-img{width:309px;height:223px;top:3420px}
.blog-cap{width:309px;text-align:center;font-size:13px;line-height:23px;color:var(--muted);top:3663px;padding:0 22px}

/* footer */
.footer{left:0;top:3767px;width:1200px;height:191px;background:var(--blue)}
.f-label{font-size:16px;font-weight:700;top:3814px;color:var(--white)}
.f-value{font-size:15px;top:3845px;color:var(--white)}
.social{top:3847px;left:879px;display:flex;gap:5px}
.social span{width:34px;height:34px;border-radius:50%;background:var(--white);display:block}
.social span.first{background:var(--green)}
.f-rule{left:171px;top:3903px;width:858px;height:1px;background:rgba(255,255,255,.35)}
.copy{left:0;top:3922px;width:1200px;text-align:center;font-size:12px;color:var(--white)}
</style>
</head>
<body>

<header class="abs site-header">
  <div class="abs brand"><span class="brand-dot"></span><span class="brand-name">Bright Path Holidays</span></div>
  <nav class="abs nav">
    <a class="active" href="#">Home</a>
    <a href="#">Cruise</a>
    <a href="#">Adventure Tours</a>
    <a href="#">Testimonials</a>
    <a href="#">About Us</a>
    <a href="#">Contact</a>
  </nav>
  <svg class="abs search" width="16" height="16" viewBox="0 0 16 16"><circle cx="6.5" cy="6.5" r="4.5" fill="none" stroke="#333" stroke-width="2"/><line x1="10" y1="10" x2="14" y2="14" stroke="#333" stroke-width="2.2"/></svg>
</header>

<section class="abs hero" role="img" aria-label="Cliffside coastal village above the sea at sunset"></section>
<h1 class="abs hero-title serif">Book</h1>
<p class="abs hero-sub serif">Unique Experiences</p>
<div class="abs hero-rule"></div>

<h2 class="abs section-title serif" style="top:765px">Popular Travel</h2>
<div class="abs tile" style="left:111px;top:856px;background:linear-gradient(180deg,#9fb9cf,#2f5b7d)" role="img" aria-label="Cruise ship on open ocean"></div>
<div class="abs tile" style="left:446px;top:856px;background:linear-gradient(180deg,#d4d6d4,#a69c8e)" role="img" aria-label="Group doing yoga on a beach"></div>
<div class="abs tile" style="left:780px;top:856px;background:linear-gradient(180deg,#4f7a4a,#8a8d86 55%,#3e6a86)" role="img" aria-label="River cruise boat by a hillside town"></div>
<div class="abs tile-label" style="left:111px;top:1100px">OCEAN CRUISES</div>
<div class="abs tile-label" style="left:446px;top:1100px">WELLNESS</div>
<div class="abs tile-label" style="left:780px;top:1100px">RIVER CRUISES</div>
<div class="abs tile" style="left:111px;top:1158px;background:linear-gradient(180deg,#8aa4b8,#4f6a82 45%,#d9d6d1)" role="img" aria-label="Breakfast table on a ship balcony"></div>
<div class="abs tile" style="left:446px;top:1158px;background:linear-gradient(180deg,#8ec6e2,#9ad0d4 50%,#e8dccb)" role="img" aria-label="Couple with a rainbow flag on a beach"></div>
<div class="abs tile" style="left:780px;top:1158px;background:linear-gradient(180deg,#c9d3d6,#6c8a4f 50%,#4e6b36)" role="img" aria-label="Hiker in a green mountain valley"></div>
<div class="abs tile-label" style="left:111px;top:1402px">LUXURY</div>
<div class="abs tile-label" style="left:446px;top:1402px">LGBTQ</div>
<div class="abs tile-label" style="left:780px;top:1402px">ADVENTURE</div>

<section class="abs about-band"></section>
<div class="abs" style="left:111px;top:1589px;width:488px;height:359px;background:linear-gradient(180deg,#3d5f8a,#9c8a6a 55%,#b7a07c)" role="img" aria-label="Ornate historic palace under a blue sky"></div>
<h2 class="abs about-title serif">About Us</h2>
<p class="abs about-text">Dedicated to helping you travel better. We are passionate about sharing our travel knowledge and first-hand insights. Sed ut perspiciatis unde omnis iste natus error sit voluptatem accu santium doloremque laudantium totam rem aperiam, eaque ipsa quae ab illo inventore veritatis et quasi architecto beatae vitae dicta sunt explica sam voluptateantium totam rem aperiam, eaque ipsa quae ab illo inventore veritatm quia.</p>

<section class="abs mag-band"></section>
<h2 class="abs mag-title serif">Award Winning Magazines</h2>
<p class="abs mag-sub">Click the magazine cover of your choice to read more.</p>
<div class="abs cover" style="left:220px;width:316px;background:linear-gradient(180deg,#c9a98a,#7e6a5c 60%,#5b6c80)" role="img" aria-label="Cruise magazine cover with couple on deck"></div>
<div class="abs cover" style="left:556px;width:423px;background:linear-gradient(180deg,#5e9cb6,#3e8fa3 55%,#2b6e86)" role="img" aria-label="Luxury travel magazine cover with infinity pool"></div>

<h2 class="abs section-title serif" style="top:2581px;font-size:33px">Our Promotions</h2>
<p class="abs section-sub" style="top:2629px">The best deals happening now. Act fast, they won't last long!</p>
<div class="abs" style="left:118px;top:2690px;width:472px;height:331px;background:linear-gradient(180deg,#a9c4d6,#8c7a6a 55%,#4a4a4a)" role="img" aria-label="Friends toasting on a cruise deck"></div>
<div class="abs" style="left:610px;top:2690px;width:472px;height:331px;background:linear-gradient(180deg,#a9bfd0,#8a8d6a 40%,#6a7b45)" role="img" aria-label="Safari vehicles and lions on a dirt road"></div>

<section class="abs blog-band"></section>
<h2 class="abs section-title serif" style="top:3189px;font-size:33px">Travel Blogs, Tips &amp; Stories</h2>
<p class="abs section-sub" style="top:3239px">Find inspiration for your next vacation of a lifetime</p>
<div class="abs btn">BOOK NOW</div>
<div class="abs blog-head" style="left:111px">GOING SOLO CRUISE SHIP</div>
<div class="abs blog-head" style="left:446px">BE ON YOUR BUCKET LIST</div>
<div class="abs blog-head" style="left:780px">THE BEST FAMILY VACATION</div>
<div class="abs blog-img" style="left:111px;background:linear-gradient(180deg,#e6e9ec,#4d8dc4 50%,#7a6a5a)" role="img" aria-label="Traveller reading on a cruise balcony"></div>
<div class="abs blog-img" style="left:446px;background:linear-gradient(180deg,#d5d8da,#8a8880 55%,#7e9a5c)" role="img" aria-label="Couple walking by historic stone buildings"></div>
<div class="abs blog-img" style="left:780px;background:linear-gradient(180deg,#2a8fd0,#3aa6d6 55%,#7a4d3a)" role="img" aria-label="Family dining beside an aquarium"></div>
<p class="abs blog-cap" style="left:111px">There are plenty of reasons people choose to travel solo by cruise ship</p>
<p class="abs blog-cap" style="left:446px">When you think of Ireland a few things often come to mind – green landscapes</p>
<p class="abs blog-cap" style="left:780px">Whether your family vacations together often or is gathering</p>

<footer class="abs footer"></footer>
<div class="abs f-label" style="left:171px">EMAIL US:</div>
<div class="abs f-value" style="left:171px">hello@brightpathholidays.ca</div>
<div class="abs f-label" style="left:578px">CALL US:</div>
<div class="abs f-value" style="left:578px">506-555-0147</div>
<div class="abs f-label" style="left:877px">FOLLOW:</div>
<div class="abs social"><span class="first"></span><span></span><span></span><span></span></div>
<div class="abs f-rule"></div>
<div class="abs copy">© 2022 BRIGHTPATHHOLIDAYS.CA</div>

</body>
</html>
```